Business Card - Tidal Lanes

Need Business Card design for company named Tidal Lanes. Software development focused mainly on Brindle Orvix & Zelt Apps. I've attached our logo with both a black and white background. Please add trademark symbol to logo when using.

```html
<!DOCTYPE html>
<html lang="en">
<head>
<meta charset="utf-8">
<title>Tidal Lanes – Business Card</title>
<link rel="stylesheet" href="https://fonts.googleapis.com/css2?family=Open+Sans:wght@400;600;700&display=swap">
<style>
  :root {
    --backdrop: #e4e4ea;
    --card: #070707;
    --white: #ffffff;
    --muted: #bdbdbd;
    --orange: #f39a2e;
    --yellow: #f7c51b;
    --red: #c8221c;
    --ink: #2a1a05;
  }
  * { box-sizing: border-box; margin: 0; padding: 0; }
  html, body { width: 1200px; height: 987px; overflow: hidden; }
  body {
    background: var(--backdrop);
    font-family: "Open Sans", Arial, sans-serif;
    position: relative;
  }
  .card {
    position: absolute;
    left: 240px;
    width: 720px;
    height: 411px;
    background: var(--card);
    border-radius: 28px;
    overflow: hidden;
    box-shadow: 0 10px 30px rgba(0,0,0,0.18);
  }
  .card--back { top: 50px; }
  .card--front { top: 526px; }

  /* Back */
  .back-brand {
    position: absolute;
    left: 0; right: 0; top: 140px;
    text-align: center;
    color: var(--white);
    font-weight: 700;
    font-size: 84px;
    letter-spacing: -2px;
    line-height: 1;
  }
  .back-web {
    position: absolute;
    left: 0; right: 0; top: 250px;
    text-align: center;
    color: var(--muted);
    font-size: 17px;
    letter-spacing: 3px;
  }

  /* Front */
  .front-brand {
    position: absolute;
    left: 60px; top: 118px;
    display: flex; align-items: center; gap: 14px;
    color: var(--white);
    font-weight: 700;
    font-size: 40px;
    letter-spacing: -1px;
  }
  .front-brand .dot {
    width: 26px; height: 26px; border-radius: 50%;
    background: var(--orange);
  }
  .divider {
    position: absolute;
    left: 360px; top: 96px;
    width: 2px; height: 130px;
    background: linear-gradient(to bottom, rgba(255,255,255,0), #d8d8d8 50%, rgba(255,255,255,0));
    transform: rotate(18deg);
  }
  .contact {
    position: absolute;
    left: 408px; top: 88px;
  }
  .contact__name {
    color: var(--orange);
    font-weight: 700;
    font-size: 30px;
    line-height: 1.1;
  }
  .contact__title {
    color: var(--white);
    font-size: 21px;
    margin-bottom: 18px;
  }
  .contact__line {
    display: flex; align-items: center; gap: 12px;
    color: var(--white);
    font-size: 24px;
    line-height: 1.45;
  }
  .contact__line svg { width: 20px; height: 20px; flex: none; }
  .band {
    position: absolute;
    left: 0; right: 0; top: 292px;
    height: 48px;
    background: linear-gradient(to right, var(--orange), var(--yellow) 60%);
    box-shadow: 0 -6px 0 -4px var(--red), 0 6px 0 -4px var(--red);
  }
  .band__address {
    position: absolute;
    left: 60px; top: 50%;
    transform: translateY(-50%);
    color: var(--ink);
    font-size: 19px;
  }
  .rule {
    position: absolute; left: 0; right: 0; height: 1px;
    background: var(--red);
  }
  .rule--top { top: 278px; }
  .rule--bottom { top: 354px; }
</style>
</head>
<body>

<section class="card card--back" aria-label="Card back">
  <div class="back-brand">Tidal Lanes</div>
  <div class="back-web">www.tidallanes.com</div>
</section>

<section class="card card--front" aria-label="Card front">
  <div class="front-brand"><span class="dot"></span>Tidal Lanes</div>
  <div class="divider"></div>
  <div class="contact">
    <div class="contact__name">Your Name</div>
    <div class="contact__title">Title</div>
    <div class="contact__line">
      <svg viewBox="0 0 20 20" aria-hidden="true"><rect x="5" y="1" width="10" height="18" rx="2" fill="var(--orange)"/><rect x="7" y="4" width="6" height="7" fill="var(--card)"/><rect x="11" y="0" width="2" height="3" fill="var(--orange)"/></svg>
      <span>555-204-7713</span>
    </div>
    <div class="contact__line">
      <svg viewBox="0 0 20 20" aria-hidden="true"><path d="M2 8 Q10 2 18 8 L16 11 L13 9 L13 7 Q10 6 7 7 L7 9 L4 11 Z" fill="var(--orange)"/><rect x="4" y="12" width="12" height="6" rx="1" fill="var(--orange)"/></svg>
      <span>555-381-0946</span>
    </div>
  </div>
  <div class="rule rule--top"></div>
  <div class="band">
    <span class="band__address">4420 Harbor Crest Rd, Tampa, FL 33602</span>
  </div>
  <div class="rule rule--bottom"></div>
</section>

</body>
</html>
```